Brochure Brightwell Hearth Partners

Brochure 12 x 9 tri fold with insert/ Rack card 9x4. Brightwell Hearth Partners 318 Corvane Street Easton, MD 21629410-822-2207AgingAtHomeSolution.com Tag: Devoted to Thoughtful Household Support.
What we do: Home care agency that services higher end Clients Artsy area on the water. Taking care of seniors in their home.

Our story: Opening Brightwell Hearth Partners, Inc. is my way of making a difference in an industry that is dominated by franchises that often have their policies dictated by corporate policy-makers who are unfamiliar with local customs. My goal is to raise the level of non-medical home health care in our area by providing additional, customized training, higher wages for our care-partners and an inclusive workforce in the decision-making process when developing customized care planning for our clients. Through collaboration with the client, their family and care-partners I have learned what issues, concerns and disappointments may arise which enables me to provide a more defined solution for those in need.My goal of providing superior training required locating a nationally recognized curriculum that would serve our clients’ needs. I found the perfect fit with Norla Vance’s, Kindred Pathway Method™ and her Shifting Stones Series™. These programs provide our care-partners with the tools needed to handle the challenges of natural aging and living with Dementia. I was so impressed with these programs, I became a Certified Independent Trainer; one of five in the State of Maryland. There is a bonus for our care-partners who are required to maintain Continuing Education Units - these programs qualify for credit! Improving our industry by providing exemplary care-partners is my goal!I look forward to assisting you with your needs! Dana Prewitt Owner

Services: Companion Care Service - Conversation and Companionship , Meal Preparation, Light House Keeping, Errand Service ,Grocery Shopping ,Incidental Transportation, Laundry & Linen Washing, Medication Reminders, Recreational Activities ,
Personal Care Services: Bathing ,Mobility ,Transferring & Positioning ,Incontinence Care ,Oral Hygiene ,Feeding, Toileting ,Grooming & Dressing, Special Diet Preparation.

Our Commitment to You: Extensive Care-Partner Education - We provide, in addition to state mandated training, eight additional hours of hands-on Dementia training from a Certified, Independent Instructor on the “Kindred Pathway Method” by Norla Vance, a nationally recognized instructor on aging.

Nutrition/Local Chef Inspired Training ;We provide six, two-hour food preparation sessions for our care-partners using local chefs, their recipes and locally grown food.

Meaningful & Engaging Activities - We provide a monthly list with local activities to our care-partners based on our client’s interest and capabilities. Focusing on what our client loved to do in the past.

Home Solutions When Needed; We provide management services to help keep our clients in their homes by working with current contractors or locating new ones to properly maintain a safe-living environment.

About owner: Dana Prewitt, owner of Brightwell Hearth Partners, has earned her certification as an Independent Trainer in the Kindred Pathway; Method (KPM) by Norla Vance, a nationally recognized instructor on natural aging and aging with Dementia. Dana is one of five certified independent trainers in the state of Maryland. All staff will have eight hours of hands on Dementia Kindred Pathway Method training.

On the insert 11x 4.25 want the top to be sticking out of the tri -fold "Dementia Experts . I would like to have shades of each STONE as it progresses
The Shifting STONES(R): The STONES model recognizes the dynamic nature of the human brain and its abilities. Unlike other cognitive models, it acknowledges that everyone’s abilities can change in a moment. Modifying environments, situations, interactions, and expectations will create either supportive positive opportunities or result in distress and a sense of failure. Just as gemstones need different settings and care to show their best characteristics, so do people. Rather than focusing on a person’s loss when there is brain change, seeing individuals as precious, unique, and capable encourages a care partnership and is the core of this model. Providing supportive settings for everyone, including care providers, allows them to use what they have to be their best. The STONES® advocate that everyone living with brain change when given the opportunity will shine. Norla Vance and Kindred Pathway Method

Sapphire ~ True Blue ~ Optimal Cognition, Healthy Brain•
True to self: personal preferences remain basically the same
• Can be flexible in thinking and appreciate multiple perspectives
• Stress/pain/fatigue may trigger Diamond state: back to Sapphire with relief
• Able to suppress and filter personal reactions: chooses effective responses
• Selects from options and can make informed decisions
• Processes well and able to successfully transition
• Aging doesn’t change ability: processing slows, more effort/time/practice needed
My brain is healthy - true blue. If I am aging normally or distressed, it may be hard for me to find words. I can describe what I am thinking so you understand. I may talk to myself because I am giving myself cues and prompts. I can learn new things and change habits, but it takes time and effort. Honoring my choices and preferences, when possible, is important. I need more time to make decisions. Give me the details and let me think about it before you need an answer. I am able to remember plans and information but supports are helpful. I may like specific prompts such as notes, calendars, and reminder calls. Health changes in vision, hearing, balance, coordination, depression, anxiety, pain, or medication may impact my behavior, but my cognitive abilities remain the same.

Diamond ~ Clear and Sharp ~ Routines and Rituals Rule
• Displays many facets: behavior and perspective can shift dramatically
• Prefers the familiar and may resist change: challenged by transitions
• More rigid and self-focused; sees wants as needs, when stressed
• Personal likes/dislikes in relationships/space/belongings etc, become more intense
• Reacts to changes in environment; benefits from familiar; functional/forgiving
• Needs repetition and time to absorb new/different information or routines
• Trusted authority figures can help: reacts better when respect is mutual
My overall cognition is clear and sharp. When happy and supported, I am capable and shine in my abilities. When distressed, I can be cutting and rigid and may see help as a threat. I have trouble seeing other points of view and may become less aware of boundaries or more possessive about my relationships, personal space, and belongings. I have many facets so people see me differently depending on the situation. This can cause conflict among my family, friends, or care team as it’s hard to tell if I am choosing my behavior or truly have limits in my ability. I can socially engage and have good cover skills. People will vary in their awareness of what is happening to me. I want to keep habits and environments as they have always been, even if they are problematic for me or others. I am often focused on the past, personal values, or finances. I will need help to make changes in my life; it’s hard for me. I can be in a Diamond state for reasons other than dementia.

Emerald ~ Green and On the Go With a Purpose ~ Naturally Flawed
• Sees self as able and independent, with limited awareness of changes in ability
• Lives in moments of clarity mixed with periods of loss in logic/reason/perspective
• Understanding and use of language change: vague words and many repeats
• Cues and support help when getting to/from places and doing daily routines
• Awareness of time, place, and situation will not always match current reality
• Strong emotional reactions are triggered by fears, desires, or unmet needs
Needs to know what comes next: seeks guidance and assistance to fill the day
I am flawed; it is part of being a natural emerald. I tend to be focused on what I want or need in this moment and may not be aware of my own safety or changing abilities. I can chat socially, but I typically miss one out of every four words and cannot accurately follow the meaning of longer conversations. I won’t remember the details of our time together, but I will remember how your body language and tone of voice made me feel. I may hide or misplace things and believe someone has taken them. My brain will make up information to fill in the blanks, which makes you think I am lying. If you try to correct me or argue, I may become resentful or suspicious of you. I am not always rational, but I don’t want to be made to feel incompetent. My brain plays tricks on me, taking me to different times and places in my life. When I am struggling, I may tell you, “I want to go home.” To provide the help and assistance I need, you must go with my flow, use a positive, partnered approach, and modify my environment.

Amber ~ Caught in a Moment of Time ~ Caution Required
• Focused on sensation: seeks to satisfy desires and tries to avoid what is disliked
•Environment can drive actions and reactions without awareness of safety
• Visual abilities are limited: focus is on pieces or parts, not the whole picture
• What happens to or around an Amber, may cause strong and surprising reactions
• Enters others’ space and crosses boundaries attempting to meet own needs
• Has periods of intense activity: may be very curious or repetitive with objects or actions
• Care is refused or seen as threatening, due to differences in perspective and ability.
Like a particle trapped in an amber, I am caught in a moment of time. It may surprise you to see how I take in the world around me. I may not know you or see you as a whole person. I react to you based on how you look, sound, move, smell, and respond to me. I like to do simple tasks over and over and may need to repeatedly move and touch, smell, taste, take or tear items apart. While it may exhaust or frustrate you, it soothes me. I don’t recognize danger; you will have to safeguard my environment. I’m intolerant to discomfort because my mouth, hands, feet, and genitalia are highly sensitive due to changes in my nervous system. Therefore, activities like eating, taking medication, mouth care, bathing, dressing, and toileting may distress me. Please notice my reaction and stop if I am resisting. I can’t help myself and one or both of us may get hurt emotionally and/or physically. If this happens, wait a few minutes, connect with me, and try a different approach; possibly substituting one area of focus for another.

Ruby ~ Deep and Strong in Color ~ Others Stop Seeing What is Possible
• Makes use of rhythm: can usually sing, hum, pray, sway, rock, clap, and dance
• When moving can’t stop; when stopped can’t get moving: needs guidance and help
• Big, strong movements are possible, while skilled abilities are being lost
• Danger exists due to limited abilities combined with automatic actions or reactions
• Tends to miss subtle hints, but gets magnified facial expressions and voice rhythms
• Can mimic actions or motions, but will struggle to understand instructions/gestures
• Able to pick up and hold objects, and yet not know what to do with them
As the deep red of a ruby masks detail, my obvious losses make my remaining abilities harder to notice. Although my fine motor skills have become very limited, remember that I am able to move and do simple things with my hands. You will need to anticipate, identify, and respond to all of my needs, even though I may not be aware of them. Plan to create a supportive environment, help with the details of care, and structure my day. Just as a crossing guard directs traffic, you will need to guide my movements and transitions. I can rarely stop or start on my own and switching gears is a challenge. Move with me first, then use your body to show me what you want me to do next, going one step at a time. Palm-beneath-Palm™ assistance helps me to feel safe and secure and to know what to do. Danger is part of my life, due to losses in visual skills, chewing abilities, balance, and coordination. You can reduce the risks to me, but not eliminate them. I can still have moments of joy when you are able to provide what gives me pleasure.

Pearl ~ Hidden Within a Shell ~ Beautiful Moments to Behold
• Will frequently recognize familiar touches, voices, faces, aromas, and tastes• Personhood survives, although all other capabilities are minimal
• Understanding input takes time: go slow and simplify for success
• In care, first get connected by offering comfort then use careful and caring touch
• Changes in the body are profound: weight loss, immobility, systems are failing
• As protective reflexes are lost, breathing, swallowing, and moving will be difficult
Care partners benefit from learning the art of letting go rather than simply giving up
While hidden like a pearl in an oyster shell, I will still have moments when I become alert and responsive. I am near the end of my life. Moments of connection create a sense of wholeness and value between us. Use our time together not just to provide care, but to comfort and connect with me. To help me complete life well, it’s important to honor my personhood when making medical or care decisions; please don’t talk about me as though I am not still here. I respond best to familiar voices and gentle rhythmic movements. I am ruled by reflexes and will startle easily. My brain is losing its ability to control and heal my body. Be prepared to see me having difficulty breathing or swallowing. My body may no longer desire food and drink as I prepare to leave this life. I may not be able to stop living without permission from you. Your greatest gift at this time in my life is to let me know that it is okay to go.

Target Market(s)

Children of seniors, seniors , rehabilitation centers

Requirements
Must have
• Nice photos of Seniors that are happy doing thing they like to do with help (Caregivers)
• Upbeat . Positive
Nice to have
• Processional looking - but very personal, we are taking care of their love ones
Should not have
• Not to feel like a cold hospital or end of life

```html
<!DOCTYPE html>
<html lang="en">
<head>
<meta charset="utf-8">
<title>Brightwell Hearth Partners – Brochure Outside</title>
<link rel="stylesheet" href="https://fonts.googleapis.com/css2?family=Montserrat:wght@400;500;600;700;800&family=Italianno&display=swap">
<style>
  :root{
    --canvas:#5b5b5b;
    --paper:#ffffff;
    --navy:#0f2f5c;
    --blue:#1665a8;
    --blue-bright:#1f7fc4;
    --blue-deep:#0b3f78;
    --ink:#1c1c1c;
    --dark-1:#111214;
    --dark-2:#3a3b3e;
    --silver:#e9ecef;
    --muted:#dcdcdc;
  }
  *{box-sizing:border-box;margin:0;padding:0}
  html,body{width:836px;height:1200px;overflow:hidden;background:var(--canvas)}
  body{font-family:"Montserrat",Arial,sans-serif;color:var(--ink)}

  .brochure{position:absolute;left:18px;top:290px;width:800px;height:620px;background:var(--paper);overflow:hidden;box-shadow:0 4px 14px rgba(0,0,0,.35)}
  .layer{position:absolute;left:0;top:0}

  /* pill headings */
  .pill{position:absolute;display:flex;align-items:center;justify-content:center;border-radius:7px;font-family:"Italianno",cursive;line-height:1}
  .pill--services{left:58px;top:222px;width:142px;height:28px;background:linear-gradient(#2d86cc,var(--blue-deep));color:#fff;font-size:28px;box-shadow:0 0 0 2px #c9dcec}
  .pill--owner{left:333px;top:196px;width:124px;height:22px;background:linear-gradient(#ffffff,#bfc3c8);color:var(--navy);font-size:24px}
  .pill--touch{left:341px;top:442px;width:120px;height:22px;background:linear-gradient(#ffffff,#c3c7cc);border-radius:7px;font-family:"Montserrat",sans-serif;font-size:12px;color:#333;letter-spacing:.2px}
  .pill--touch b{color:var(--blue);font-weight:700;margin-right:4px}

  /* services */
  .services{position:absolute;left:35px;width:220px}
  .services--companion{top:264px}
  .services--personal{top:428px}
  .services h3{font-size:11.5px;font-weight:700;color:var(--ink);margin-bottom:4px;letter-spacing:.1px}
  .services h3 span{color:var(--blue)}
  .services li{list-style:none;position:relative;padding-left:19px;font-size:9.6px;line-height:14.5px;color:#222}
  .services li::before{content:"";position:absolute;left:2px;top:3px;width:8px;height:8px;border:1px solid #444;border-radius:50%}
  .services li::after{content:"";position:absolute;left:5px;top:5px;width:2px;height:4px;border:solid #444;border-width:0 1px 1px 0;transform:rotate(40deg)}

  /* middle panel */
  .about{position:absolute;left:288px;top:208px;width:216px;height:146px;border:1px dashed #9a9a9a;border-radius:6px;padding:17px 8px 6px;font-size:8.3px;line-height:11.7px;font-style:italic;color:#eee;text-align:justify}
  .brand{position:absolute;font-weight:500;color:var(--navy);line-height:1.05;white-space:nowrap}
  .brand--mid{left:262px;width:263px;top:382px;text-align:center;color:#e8e8e8;font-size:17px}
  .brand--cover{right:22px;top:24px;text-align:right;font-size:20px;color:var(--blue)}
  .contact{position:absolute;left:262px;width:263px;top:524px;text-align:center;color:#eee;font-size:8.4px;line-height:11.5px}
  .contact .phone{font-weight:700;font-size:11.5px;line-height:15px;color:#fff}
  .contact .web{font-size:10px}
  .icons{position:absolute;left:356px;top:485px;display:flex;gap:10px}
  .icons span{width:20px;height:20px;border-radius:50%;background:var(--blue-bright);display:flex;align-items:center;justify-content:center}

  /* cover */
  .tagline{position:absolute;left:525px;width:275px;top:446px;text-align:center;font-weight:800;font-size:20px;line-height:24px;text-transform:uppercase;color:var(--navy);white-space:nowrap}
  .tagline span{color:var(--blue)}
  .cover-copy{position:absolute;left:525px;width:275px;top:546px;text-align:center;font-size:9.6px;line-height:13px;color:#222}

  /* footer */
  .footer{position:absolute;left:0;bottom:0;width:800px;height:26px;background:linear-gradient(90deg,var(--blue-deep),#2b78bf 50%,var(--blue-deep));display:flex}
  .footer span{flex:0 0 auto;display:flex;align-items:center;justify-content:center;color:#e7f0fa;font-size:9.5px;letter-spacing:.6px}
  .footer span:nth-child(1){width:262px}
  .footer span:nth-child(2){width:263px}
  .footer span:nth-child(3){width:275px}
</style>
</head>
<body>
<main class="brochure">

  <!-- background structure -->
  <svg class="layer" width="800" height="620" viewBox="0 0 800 620" aria-hidden="true">
    <defs>
      <linearGradient id="darkPanel" x1="0" y1="0" x2="0" y2="1">
        <stop offset="0" stop-color="#0c0d0f"/>
        <stop offset=".55" stop-color="#2a2b2e"/>
        <stop offset="1" stop-color="#444548"/>
      </linearGradient>
      <linearGradient id="swoosh" x1="0" y1="0" x2="1" y2="1">
        <stop offset="0" stop-color="#0b3f78"/>
        <stop offset=".5" stop-color="#1f74bb"/>
        <stop offset="1" stop-color="#0d4585"/>
      </linearGradient>
      <linearGradient id="leftFade" x1="0" y1="0" x2="0" y2="1">
        <stop offset="0" stop-color="#ffffff"/>
        <stop offset=".6" stop-color="#f3f5f7"/>
        <stop offset="1" stop-color="#e6e9ec"/>
      </linearGradient>
    </defs>
    <rect x="0" y="0" width="262" height="620" fill="url(#leftFade)"/>
    <rect x="262" y="0" width="263" height="620" fill="url(#darkPanel)"/>
    <!-- top swoosh -->
    <path d="M240,0 H520 C545,60 620,100 800,108 V150 C700,146 610,128 525,140 L525,0 Z" fill="url(#swoosh)"/>
    <path d="M525,0 C550,56 622,94 800,100 V106 C620,98 546,60 520,0 Z" fill="#ffffff"/>
    <path d="M520,140 C610,124 700,136 800,142 V150 C700,146 610,134 525,146 Z" fill="#222"/>
    <!-- left photo blue rim sweeping into middle -->
    <path d="M0,186 C70,228 200,225 262,168 C292,140 300,70 330,0 H262 V0 Z" fill="url(#swoosh)"/>
  </svg>

  <!-- left panel photo -->
  <svg class="layer" width="262" height="220" viewBox="0 0 262 220" role="img" aria-label="Photo: smiling senior woman seated at home with a caregiver in scrubs holding a clipboard">
    <defs>
      <linearGradient id="photoLeft" x1="0" y1="0" x2="1" y2="1">
        <stop offset="0" stop-color="#b89a7c"/>
        <stop offset=".5" stop-color="#e2d6c8"/>
        <stop offset="1" stop-color="#8fa6c0"/>
      </linearGradient>
    </defs>
    <path d="M0,0 H262 V150 C205,212 70,214 0,172 Z" fill="url(#photoLeft)"/>
  </svg>

  <!-- middle badge: plain seal shape -->
  <svg class="layer" width="800" height="200" viewBox="0 0 800 200" aria-hidden="true" style="pointer-events:none">
    <circle cx="393" cy="96" r="72" fill="#c9ced4"/>
    <circle cx="393" cy="96" r="66" fill="#12366a"/>
    <circle cx="393" cy="96" r="46" fill="#ffffff" stroke="#d9dde2" stroke-width="2"/>
  </svg>

  <!-- right cover photo -->
  <svg class="layer" width="800" height="450" viewBox="0 0 800 450" role="img" aria-label="Photo: happy senior woman in a wheelchair sharing a laugh with her caregiver beside a decorated tree" style="pointer-events:none">
    <defs>
      <linearGradient id="photoRight" x1="0" y1="0" x2="1" y2="1">
        <stop offset="0" stop-color="#6b7d5a"/>
        <stop offset=".45" stop-color="#d8c8b4"/>
        <stop offset="1" stop-color="#9ab0cc"/>
      </linearGradient>
    </defs>
    <path d="M525,146 C610,134 700,142 800,150 V396 C720,430 610,432 525,408 Z" fill="url(#photoRight)"/>
    <path d="M525,408 C610,432 720,430 800,396" fill="none" stroke="#1665a8" stroke-width="5"/>
    <path d="M540,420 C630,442 730,436 800,408" fill="none" stroke="#0f2f5c" stroke-width="1.5" opacity=".6"/>
  </svg>

  <!-- left panel: services -->
  <h2 class="pill pill--services">Our Services</h2>

  <section class="services services--companion">
    <h3>COMPANION <span>CARE SERVICE</span></h3>
    <ul>
      <li>Conversation &amp; Companionship</li>
      <li>Meal Preparation</li>
      <li>Light House Keeping</li>
      <li>Errand Service</li>
      <li>Grocery Shopping</li>
      <li>Incidental Transportation</li>
      <li>Laundry &amp; Linen Washing</li>
      <li>Medication Reminders</li>
      <li>Recreational Activities</li>
    </ul>
  </section>

  <section class="services services--personal">
    <h3>PERSONAL <span>CARE SERVICE</span></h3>
    <ul>
      <li>Bathing</li>
      <li>Mobility</li>
      <li>Transferring &amp; Positioning</li>
      <li>Incontinence Care</li>
      <li>Oral Hygiene</li>
      <li>Feeding</li>
      <li>Toileting</li>
      <li>Grooming &amp; Dressing</li>
      <li>Special Diet Preparation</li>
    </ul>
  </section>

  <!-- middle panel: owner & contact -->
  <p class="about">Dana Prewitt, owner of Brightwell Hearth Partners, has earned her certification as an Independent Trainer in the Kindred Pathway Method&reg; (KPM) by Norla Vance, a nationally recognized instructor on natural aging and aging with Dementia. Dana is one of five certified independent trainers in the state of Maryland. All staff will have eight hours of hands on Dementia Kindred Pathway Method training.</p>
  <h2 class="pill pill--owner">About Owner</h2>

  <p class="brand brand--mid">Brightwell<br>Hearth Partners</p>

  <p class="pill pill--touch"><b>GET IN</b> TOUCH</p>

  <div class="icons" aria-hidden="true">
    <span><svg width="10" height="12" viewBox="0 0 10 12"><path d="M5,0 C2.2,0 0,2.1 0,4.7 C0,8 5,12 5,12 C5,12 10,8 10,4.7 C10,2.1 7.8,0 5,0 Z" fill="#fff"/><circle cx="5" cy="4.6" r="1.8" fill="#1f7fc4"/></svg></span>
    <span><svg width="8" height="12" viewBox="0 0 8 12"><rect x=".5" y=".5" width="7" height="11" rx="1.5" fill="#fff"/><rect x="1.8" y="2" width="4.4" height="6.5" fill="#1f7fc4"/><circle cx="4" cy="10" r=".8" fill="#1f7fc4"/></svg></span>
    <span><svg width="12" height="12" viewBox="0 0 12 12" fill="none" stroke="#fff" stroke-width="1"><circle cx="6" cy="6" r="5"/><ellipse cx="6" cy="6" rx="2.2" ry="5"/><path d="M1,6 H11 M1.8,3.5 H10.2 M1.8,8.5 H10.2"/></svg></span>
  </div>

  <address class="contact" style="font-style:normal">
    318 Corvane Street<br>
    Easton, MD 21774<br>
    <span class="phone">410-555-0148</span><br>
    <span class="web">www.brightwellhearthpartners.example</span>
  </address>

  <!-- right panel: cover -->
  <p class="brand brand--cover">Brightwell<br>Hearth Partners</p>

  <h1 class="tagline">Devoted to<br><span>Thoughtful<br>Household Support</span></h1>
  <p class="cover-copy">Home care agency that services higher end<br>Clients. Taking care of seniors in their home.</p>

  <footer class="footer">
    <span>BrightwellHearthPartners.example</span>
    <span>BrightwellHearthPartners.example</span>
    <span>BrightwellHearthPartners.example</span>
  </footer>
</main>
</body>
</html>
```